Business Card Design

We need the business card for our new business based in St. Marys, we manufacture mainly bubble wraps. And we would like the design to use our company logo and also make it easy for people to understand right away we are bubble wrap manufacturer

Industry/Entity Type

Business

Contact Information for Business Card

Cushtane Pty Ltd, 14 Larkin Road Orchard Vale NSW 2789, Tel: 02 9471 5826, Fax: 9471 5839, Dara Oyelaran, General Manager, Mobile :0438 217 564, dara.oyelaran@cushtane.com.au, Website: cushtane.com.au

```html
<!DOCTYPE html>
<html lang="en">
<head>
<meta charset="utf-8">
<title>Cushtane Business Card</title>
<link href="https://fonts.googleapis.com/css2?family=Roboto:wght@300;400;700&display=swap" rel="stylesheet">
<style>
  :root {
    --page: #ecebe9;
    --white: #ffffff;
    --grey: #5f6062;
    --ink: #4f5052;
    --red: #b01a28;
  }
  * { margin: 0; padding: 0; box-sizing: border-box; }
  html, body { width: 1200px; height: 848px; overflow: hidden; }
  body {
    background: var(--page);
    font-family: "Roboto", Arial, sans-serif;
    color: var(--ink);
    position: relative;
  }
  .card {
    position: absolute;
    top: 259px;
    width: 540px;
    height: 330px;
    background: var(--white);
    box-shadow: 0 4px 14px rgba(0,0,0,0.12);
    overflow: hidden;
  }
  .card--front { left: 50px; }
  .card--back { left: 610px; background: var(--grey); }

  .band { position: absolute; }
  .band--left-grey { left: 0; top: 0; width: 44px; height: 330px; background: var(--grey); }
  .band--left-red { left: 0; top: 186px; width: 44px; height: 44px; background: var(--red);
    border-top: 4px solid var(--white); border-bottom: 4px solid var(--white); box-sizing: content-box; }
  .band--right-grey { right: 0; top: 0; width: 40px; height: 330px; background: var(--grey); }
  .band--right-red { right: 0; top: 44px; width: 40px; height: 30px; background: var(--red);
    border-top: 4px solid var(--white); border-bottom: 4px solid var(--white); box-sizing: content-box; }
  .band--feature { right: 0; top: 128px; width: 250px; height: 40px; background: var(--red);
    border-top: 4px solid var(--white); border-bottom: 4px solid var(--white); box-sizing: content-box; }

  .holder { position: absolute; right: 58px; top: 34px; text-align: right; }
  .holder__name { font-size: 25px; font-weight: 400; letter-spacing: -0.5px; line-height: 1; }
  .holder__role { font-size: 10px; font-weight: 400; margin-top: 2px; }

  .brand-name {
    position: absolute; left: 78px; top: 190px;
    font-weight: 700; font-size: 32px; letter-spacing: 1px;
    color: var(--grey); line-height: 1;
  }

  .phones { position: absolute; left: 80px; top: 248px; list-style: none; }
  .phones li { display: flex; align-items: center; gap: 14px; height: 24px;
    font-size: 17px; font-weight: 300; }
  .phones svg { width: 16px; height: 16px; fill: var(--ink); }

  .contacts { position: absolute; right: 46px; top: 184px; list-style: none; text-align: right; }
  .contacts li { display: flex; justify-content: flex-end; align-items: flex-start; gap: 10px;
    font-size: 12.5px; font-weight: 300; line-height: 15px; margin-bottom: 4px; }
  .contacts svg { width: 12px; height: 12px; fill: var(--ink); flex: none; margin-top: 2px; }
  .contacts .spacer { width: 12px; flex: none; }

  .back__frame { position: absolute; inset: 20px; background: var(--red); }
  .back__panel { position: absolute; inset: 30px; background: var(--white);
    display: flex; align-items: center; justify-content: center; }
  .back__name { font-weight: 700; font-size: 62px; letter-spacing: 2px; color: var(--grey); }
</style>
</head>
<body>

<section class="card card--front" aria-label="Business card front">
  <div class="band band--left-grey"></div>
  <div class="band band--left-red"></div>
  <div class="band band--right-grey"></div>
  <div class="band band--right-red"></div>
  <div class="band band--feature"></div>

  <div class="holder">
    <p class="holder__name">Dara Oyelaran</p>
    <p class="holder__role">General Manager</p>
  </div>

  <p class="brand-name">CUSHTANE</p>

  <ul class="phones">
    <li>
      <svg viewBox="0 0 24 24" aria-label="Telephone"><path d="M6.6 10.8a15.1 15.1 0 0 0 6.6 6.6l2.2-2.2c.3-.3.7-.4 1-.2 1.1.4 2.3.6 3.6.6.6 0 1 .4 1 1V20c0 .6-.4 1-1 1A17 17 0 0 1 3 4c0-.6.4-1 1-1h3.5c.6 0 1 .4 1 1 0 1.3.2 2.5.6 3.6.1.3 0 .7-.2 1z"/></svg>
      <span>02 9471 5826</span>
    </li>
    <li>
      <svg viewBox="0 0 24 24" aria-label="Mobile"><path d="M7 1h10a2 2 0 0 1 2 2v18a2 2 0 0 1-2 2H7a2 2 0 0 1-2-2V3a2 2 0 0 1 2-2zm0 3v15h10V4zm5 16.2a.9.9 0 1 0 0 1.8.9.9 0 0 0 0-1.8z"/></svg>
      <span>0438 217 564</span>
    </li>
    <li>
      <svg viewBox="0 0 24 24" aria-label="Fax"><path d="M6 2h12v5H6zM3 8h18a2 2 0 0 1 2 2v7h-4v5H5v-5H1v-7a2 2 0 0 1 2-2zm4 8v4h10v-4z"/></svg>
      <span>9471 5839</span>
    </li>
  </ul>

  <ul class="contacts">
    <li><span>cushtane.com.au</span>
      <svg viewBox="0 0 24 24" aria-label="Website"><path d="M2 3h20v14H13v2h4v2H7v-2h4v-2H2zm2 2v10h16V5z"/></svg></li>
    <li><span>dara.oyelaran@cushtane.com.au</span>
      <svg viewBox="0 0 24 24" aria-label="Email"><path d="M2 5h20v14H2zm2 2v.5l8 5 8-5V7z"/></svg></li>
    <li><span>Cushtane Pty Ltd, 14 Larkin Road</span>
      <svg viewBox="0 0 24 24" aria-label="Address"><path d="M12 1a7 7 0 0 1 7 7c0 5-7 15-7 15S5 13 5 8a7 7 0 0 1 7-7zm0 4a3 3 0 1 0 0 6 3 3 0 0 0 0-6z"/></svg></li>
    <li><span>Orchard Vale NSW 2789</span><span class="spacer"></span></li>
  </ul>
</section>

<section class="card card--back" aria-label="Business card back">
  <div class="back__frame"></div>
  <div class="back__panel">
    <p class="back__name">CUSHTANE</p>
  </div>
</section>

</body>
</html>
```